Postcard for dumpster rental business

We need an attractive post card to entice other businesses to use our dumpster rental service. This is a business to business situation.
Target Market(s)
Roofing, property restoration and remodeling contractors
Industry/Entity Type
Dumpster rentals
Font styles to use
Sans Serif
Colors
0054AA
0677BA
7BADD7
CADEEF
E8F1F8
Requirements
Must have
- 42goskips.net Dumpster rental Easy online booking Logo Guaranteed On Time Delivery (as a badge or button?) QR Code Picture of our dumpster (see website)
Nice to have
- Call to action "Order now!"

```html
<!DOCTYPE html>
<html lang="en">
<head>
<meta charset="utf-8">
<title>42go Skip Rental – Postcard</title>
<link rel="stylesheet" href="https://fonts.googleapis.com/css2?family=Montserrat:wght@600;700;800;900&family=Poppins:wght@400;500;600;700&family=Oswald:wght@500&display=swap">
<style>
  :root{
    --navy:#16386b;
    --navy-deep:#0f2a55;
    --blue:#0054AA;
    --blue-mid:#0677BA;
    --blue-card:#2a6fb0;
    --blue-light:#7BADD7;
    --blue-pale:#CADEEF;
    --blue-wash:#E8F1F8;
    --orange:#f26b0f;
    --orange-bright:#ff7a1a;
    --ink:#222326;
    --grey-bar:#7d7f84;
    --stamp:#dcdcdc;
    --white:#ffffff;
    --page:#f4f4f4;
  }
  *{box-sizing:border-box;margin:0;padding:0}
  html,body{width:1200px;height:2512px;overflow:hidden;background:var(--page)}
  body{position:relative;font-family:"Poppins",Arial,sans-serif}

  .postcard{position:absolute;left:100px;width:1000px;height:665px;overflow:hidden;background:var(--white);box-shadow:0 8px 28px rgba(0,0,0,.18)}
  .postcard--front{top:420px}
  .postcard--back{top:1260px}
  .shapes{position:absolute;inset:0;width:100%;height:100%}

  /* brand lockup */
  .brand{position:absolute;display:flex;align-items:center;gap:10px;font-family:"Montserrat",Arial,sans-serif;font-weight:800;white-space:nowrap}
  .brand__mark{width:18px;height:18px;background:currentColor;display:inline-block}

  /* ---------- front ---------- */
  .front-brand{left:46px;top:40px;color:var(--white);font-size:24px}
  .headline{position:absolute;left:46px;top:135px;color:var(--white);font-family:"Montserrat",Arial,sans-serif;font-weight:900;font-size:41px;line-height:1.1;letter-spacing:.2px}
  .order-now{position:absolute;left:48px;top:293px;color:var(--white);font-family:"Montserrat",Arial,sans-serif;font-weight:800;font-size:50px}
  .feature{position:absolute;text-align:center;font-family:"Poppins",Arial,sans-serif;font-weight:500;font-size:30px;line-height:1.35;color:var(--ink)}
  .feature em{font-style:normal;color:var(--orange);font-weight:600}
  .feature svg{display:block;margin:0 auto 6px}
  .feature--booking{left:40px;top:395px;width:230px}
  .feature--delivery{left:280px;top:395px;width:300px}
  .feature-divider{position:absolute;left:254px;top:410px;height:130px;border-left:2px dotted #8a8a8a}
  .photo-circle{position:absolute;left:507px;top:2px;width:572px;height:572px;border-radius:50%;
    background:radial-gradient(circle at 45% 40%,#f28a2e 0%,#e0661a 30%,#2f6fb3 62%,#1c4f92 100%);
    box-shadow:0 0 0 6px var(--white),0 0 0 11px var(--blue-mid)}
  .front-phone{position:absolute;left:40px;top:596px;display:flex;align-items:center;gap:14px;color:var(--white);font-weight:600;font-size:44px}
  .front-web{position:absolute;left:474px;top:612px;display:flex;align-items:center;gap:12px;color:var(--white);font-size:36px;font-weight:400}
  .front-web em{font-style:normal;color:var(--orange-bright)}

  /* ---------- back ---------- */
  .back-title{position:absolute;left:45px;top:36px;color:var(--white);font-family:"Montserrat",Arial,sans-serif;font-weight:800;font-size:44px}
  .price-row{position:absolute;left:48px;width:470px;height:72px;display:flex;align-items:center}
  .price-row--10{top:98px}
  .price-row--15{top:182px}
  .price-row--20{top:272px}
  .price-row__thumb{width:134px;height:52px;background:linear-gradient(180deg,#f7862a,#d65a0c);clip-path:polygon(0 0,100% 0,96% 100%,4% 100%)}
  .price-row__size{margin-left:18px;width:84px;text-align:center;color:var(--white);font-family:"Montserrat",Arial,sans-serif;font-weight:700;font-size:18px;line-height:.9}
  .price-row__size small{display:block;font-size:10px;font-weight:700}
  .price-row__price{margin-left:18px;color:var(--white);font-family:"Oswald",Arial,sans-serif;font-weight:500;font-size:26px}
  .price-row__dims{margin-left:16px;text-align:center;color:var(--white);font-family:"Montserrat",Arial,sans-serif;font-weight:700;font-size:10px;line-height:1.5}
  .price-rule{position:absolute;left:50px;width:445px;border-top:1px dashed var(--blue-light)}
  .notice{position:absolute;left:42px;top:364px;font-family:"Poppins",Arial,sans-serif;font-size:13.5px;line-height:1.3;color:var(--white);font-weight:600}
  .notice strong{display:block;color:var(--orange-bright);font-size:15.5px;font-weight:600}
  .map-area{position:absolute;left:16px;top:440px;width:236px;height:104px;border-radius:50%;background:radial-gradient(ellipse at center,#a9cde8 0%,#d7e8f3 55%,#eef4f8 100%)}
  .map-pin{position:absolute;left:109px;top:425px}
  .service{position:absolute;left:264px;top:442px;width:250px}
  .service__title{color:var(--orange);font-family:"Montserrat",Arial,sans-serif;font-weight:700;font-size:14.5px;line-height:1.3}
  .service__text{margin-top:8px;color:var(--ink);font-size:10px;font-weight:600;line-height:1.35}
  .service__button{display:inline-block;margin-top:8px;background:var(--orange);color:var(--white);font-size:10px;font-weight:600;padding:4px 18px;border-radius:12px}
  .back-contact{position:absolute;left:46px;top:588px;color:var(--white)}
  .back-contact__line{display:flex;align-items:center;gap:10px}
  .back-contact__phone{font-size:26px;font-weight:600}
  .back-contact__web{font-size:20px;font-weight:600;margin-top:2px}
  .back-brand{left:612px;top:52px;color:var(--blue-mid);font-size:22px}
  .stamp{position:absolute;left:865px;top:45px;width:92px;height:104px;background:var(--stamp)}
  .address-line{position:absolute;left:630px;width:282px;border-top:1.5px solid #9a9a9a}
</style>
</head>
<body>

<!-- FRONT -->
<section class="postcard postcard--front" aria-label="Postcard front">
  <svg class="shapes" viewBox="0 0 1000 665" preserveAspectRatio="none" aria-hidden="true">
    <defs>
      <linearGradient id="frontSky" x1="0" y1="0" x2="1" y2="0">
        <stop offset="0" stop-color="#1b4a86"/>
        <stop offset="1" stop-color="#2564a8"/>
      </linearGradient>
    </defs>
    <rect x="0" y="0" width="1000" height="370" fill="url(#frontSky)"/>
    <polygon points="0,0 290,0 330,70 0,70" fill="var(--navy-deep)"/>
    <rect x="0" y="70" width="330" height="0" fill="var(--navy-deep)"/>
    <polygon points="318,35 640,35 615,62 340,62" fill="var(--orange)"/>
    <rect x="0" y="275" width="600" height="95" fill="var(--orange)"/>
    <rect x="0" y="370" width="1000" height="205" fill="var(--white)"/>
    <polygon points="0,575 440,575 470,665 0,665" fill="var(--blue-card)"/>
    <polygon points="440,595 1000,595 1000,665 470,665" fill="var(--ink)"/>
  </svg>

  <div class="brand front-brand"><span class="brand__mark"></span>42go Skip Rental</div>
  <h1 class="headline">DUMPSTER RENTAL<br>AND REMOVAL<br>SERVICES</h1>
  <div class="order-now">ORDER NOW!</div>

  <div class="photo-circle" role="img" aria-label="Photo of a worker loading debris into an orange roll-off dumpster"></div>

  <div class="feature feature--booking">
    <svg width="48" height="56" viewBox="0 0 48 56" aria-hidden="true">
      <rect x="12" y="2" width="24" height="42" rx="3" fill="none" stroke="#2a2a2a" stroke-width="3"/>
      <rect x="17" y="10" width="14" height="20" fill="#2a2a2a"/>
      <circle cx="10" cy="14" r="8" fill="#2a2a2a"/>
      <path d="M6 14l3 3 5-6" fill="none" stroke="#fff" stroke-width="2"/>
      <path d="M26 30v18h14V36l-6-2-4 0z" fill="#2a2a2a"/>
    </svg>
    Easy <em>online</em><br><em>booking</em>
  </div>
  <div class="feature-divider"></div>
  <div class="feature feature--delivery">
    <svg width="92" height="48" viewBox="0 0 92 48" aria-hidden="true">
      <path d="M16 8h40v28H16zM56 16h14l10 10v10H56z" fill="#2a2a2a"/>
      <rect x="2" y="14" width="10" height="3" fill="#2a2a2a"/>
      <rect x="0" y="22" width="12" height="3" fill="#2a2a2a"/>
      <circle cx="28" cy="38" r="6" fill="#fff" stroke="#2a2a2a" stroke-width="3"/>
      <circle cx="68" cy="38" r="6" fill="#fff" stroke="#2a2a2a" stroke-width="3"/>
      <circle cx="82" cy="14" r="9" fill="#2a2a2a"/>
      <path d="M77 14l3 3 6-6" fill="none" stroke="#fff" stroke-width="2"/>
    </svg>
    Guaranteed <em>On</em><br><em>Time Delivery</em>
  </div>

  <div class="front-phone">
    <svg width="34" height="34" viewBox="0 0 24 24" aria-hidden="true"><path d="M6.6 10.8a15 15 0 006.6 6.6l2.2-2.2a1 1 0 011-.25 11.4 11.4 0 003.6.57 1 1 0 011 1V20a1 1 0 01-1 1A17 17 0 013 4a1 1 0 011-1h3.5a1 1 0 011 1c0 1.25.2 2.45.57 3.57a1 1 0 01-.25 1z" fill="var(--orange-bright)"/></svg>
    (555) 014-2290
  </div>
  <div class="front-web">
    <svg width="28" height="28" viewBox="0 0 24 24" aria-hidden="true"><circle cx="12" cy="12" r="10" fill="var(--orange)"/><path d="M2 12h20M12 2c3 3 3 17 0 20M12 2c-3 3-3 17 0 20" stroke="var(--ink)" stroke-width="1.5" fill="none"/></svg>
    <span>www.<em>42goskips</em>.net</span>
  </div>
</section>

<!-- BACK -->
<section class="postcard postcard--back" aria-label="Postcard back">
  <svg class="shapes" viewBox="0 0 1000 665" preserveAspectRatio="none" aria-hidden="true">
    <path d="M0 0H430Q585 110 575 345H0Z" fill="var(--blue-card)"/>
    <path d="M0 345H590L568 425H0Z" fill="var(--navy-deep)"/>
    <path d="M575 345L590 362L580 345Z" fill="var(--navy)"/>
    <path d="M564 425Q530 560 402 665" fill="none" stroke="var(--blue-card)" stroke-width="5"/>
    <path d="M0 575H492Q455 625 402 665H0Z" fill="var(--grey-bar)"/>
  </svg>

  <h2 class="back-title">DUMPSTERS</h2>

  <div class="price-row price-row--10">
    <div class="price-row__thumb" role="img" aria-label="10 yard dumpster photo"></div>
    <div class="price-row__size">10 YARD<small>DUMPSTER</small></div>
    <div class="price-row__price">$318.00</div>
    <div class="price-row__dims">DIMENSIONS<br>14' L X 7' W X 2.8' H</div>
  </div>
  <div class="price-rule" style="top:172px"></div>
  <div class="price-row price-row--15">
    <div class="price-row__thumb" role="img" aria-label="15 yard dumpster photo"></div>
    <div class="price-row__size">15 YARD<small>DUMPSTER</small></div>
    <div class="price-row__price">$358.00</div>
    <div class="price-row__dims">DIMENSIONS<br>16' L X 7' W X 3.6' H</div>
  </div>
  <div class="price-rule" style="top:262px"></div>
  <div class="price-row price-row--20">
    <div class="price-row__thumb" role="img" aria-label="20 yard dumpster photo"></div>
    <div class="price-row__size">20 YARD<small>DUMPSTER</small></div>
    <div class="price-row__price">$398.00</div>
    <div class="price-row__dims">DIMENSIONS<br>16' L X 7' W X 5' H</div>
  </div>

  <p class="notice"><strong>If you don't see your city listed above, just let us know!</strong>Accommodations can usually be made to suit your project and your budget.</p>

  <div class="map-area" role="img" aria-label="Map of the rental service area"></div>
  <svg class="map-pin" width="34" height="48" viewBox="0 0 34 48" aria-hidden="true"><path d="M17 46L5 24a14 14 0 1124 0z" fill="var(--orange)"/><circle cx="17" cy="15" r="9" fill="var(--white)"/></svg>

  <div class="service">
    <div class="service__title">42GO SKIP<br>RENTAL SERVICE AREA</div>
    <p class="service__text">We provide fast, friendly services in Wayne, Oakland, and Macomb County Communities. To see if your city is included, please click the link below.</p>
    <span class="service__button">View service area</span>
  </div>

  <div class="back-contact">
    <div class="back-contact__line back-contact__phone">
      <svg width="18" height="18" viewBox="0 0 24 24" aria-hidden="true"><path d="M6.6 10.8a15 15 0 006.6 6.6l2.2-2.2a1 1 0 011-.25 11.4 11.4 0 003.6.57 1 1 0 011 1V20a1 1 0 01-1 1A17 17 0 013 4a1 1 0 011-1h3.5a1 1 0 011 1c0 1.25.2 2.45.57 3.57a1 1 0 01-.25 1z" fill="var(--orange-bright)"/></svg>
      (555) 014-2290
    </div>
    <div class="back-contact__line back-contact__web">
      <svg width="18" height="18" viewBox="0 0 24 24" aria-hidden="true"><circle cx="12" cy="12" r="10" fill="var(--orange)"/></svg>
      www.42goskips.net
    </div>
  </div>

  <div class="brand back-brand"><span class="brand__mark"></span>42go Skip Rental</div>
  <div class="stamp"></div>
  <div class="address-line" style="top:285px"></div>
  <div class="address-line" style="top:342px"></div>
  <div class="address-line" style="top:400px"></div>
</section>

</body>
</html>
```